Business Card & Email Signature Design || Upmarket + Luxury

Rima Vale Honey, a New Zealand Manuka Honey company needs a Business Card & Email Signature design.

Our logo's are attached in Gold & Black versions, feel free to be creative with how you use the logo and it's patterns in your design.

Style:
- Looking for an Elegant, Luxurious, Upmarket feel.
- Black/Matte Black Card, Gold Foil, UV Embossing

Information to Add:

- Logo
- Company Name: Rima Vale Honey
- Name: Martin Holloway
- Title: Creative Director
- Phone: +64 2815 96 417
- Email: martin@rimavalehoney.example.nz
- Website: www.rimavalehoney.example.nz

- Socials: ***For email Signature Only***
- Facebook: https://www.facebook.com/rimavalehoney/
- Instagram: https://www.instagram.com/rimavalehoney/

Target Market(s)

Asia/Europe Luxury, Upmarket

Contact Information for Business Card

- Logo
- Name: Martin Holloway
- Phone: +64 2815 96 417

Font styles to use
Other font styles liked:
• Champagne & Limousines (Attached)

Requirements
Must have
• Business Card & Email Signature Design.

Looking for a Sleek, Luxury, Upmarket Design.

```html
<!DOCTYPE html>
<html lang="en">
<head>
<meta charset="utf-8">
<title>Rima Vale Honey — Business Card</title>
<link rel="stylesheet" href="https://fonts.googleapis.com/css2?family=Montserrat:wght@400;700&display=swap">
<style>
  :root {
    --backdrop: #2a2422;
    --card-black: #0d0d0d;
    --card-edge: #1a1a1a;
    --gold-light: #f3dc8e;
    --gold-mid: #d4b45a;
    --gold-deep: #a9822e;
    --gold-text: #dcbd6a;
    --rule: #4a3f2a;
  }
  * { margin: 0; padding: 0; box-sizing: border-box; }
  html, body { width: 1200px; height: 842px; overflow: hidden; }
  body {
    background: var(--backdrop);
    font-family: "Montserrat", sans-serif;
    color: var(--gold-text);
    position: relative;
  }
  .card {
    position: absolute;
    top: 272px;
    width: 520px;
    height: 297px;
    background: radial-gradient(ellipse at 40% 40%, #161616, var(--card-black));
    border: 1px solid var(--card-edge);
    box-shadow: 0 14px 30px rgba(0,0,0,0.55);
    overflow: hidden;
  }
  .card--back { left: 50px; }
  .card--front { left: 630px; }

  .gold-band {
    position: absolute;
    left: 0;
    width: 100%;
    height: 11px;
    background: linear-gradient(90deg, var(--gold-deep), var(--gold-light) 45%, var(--gold-mid) 70%, var(--gold-light));
  }
  .gold-band--top { top: 10px; }
  .gold-band--bottom { bottom: 10px; }

  .contact {
    position: absolute;
    inset: 0;
    display: flex;
    flex-direction: column;
    align-items: center;
    justify-content: center;
    text-align: center;
  }
  .contact__name {
    font-weight: 700;
    font-size: 20px;
    letter-spacing: 0.3px;
    text-transform: uppercase;
  }
  .contact__title {
    font-size: 14px;
    margin-top: 1px;
  }
  .contact__rule {
    width: 120px;
    height: 1px;
    background: var(--rule);
    margin: 14px 0 12px;
  }
  .contact__line {
    font-size: 14px;
    line-height: 1.35;
  }

  .gold-tab {
    position: absolute;
    width: 54px;
    height: 30px;
    background: linear-gradient(180deg, var(--gold-light), var(--gold-mid) 60%, var(--gold-deep));
  }
  .gold-tab--left { left: 0; top: 172px; }
  .gold-tab--right { right: 0; top: 70px; }

  .brand {
    position: absolute;
    inset: 0;
    display: flex;
    align-items: center;
    justify-content: center;
    gap: 16px;
  }
  .brand__dot {
    width: 26px;
    height: 26px;
    border-radius: 50%;
    border: 1.5px solid var(--gold-text);
  }
  .brand__name {
    font-weight: 400;
    font-size: 22px;
    letter-spacing: 4px;
    text-transform: uppercase;
    color: var(--gold-text);
  }
</style>
</head>
<body>
  <section class="card card--back" aria-label="Business card, contact side">
    <div class="gold-band gold-band--top"></div>
    <div class="contact">
      <p class="contact__name">Martin Holloway</p>
      <p class="contact__title">Creative Director</p>
      <div class="contact__rule"></div>
      <p class="contact__line">+64 2815 96 417</p>
      <p class="contact__line">martin@rimavalehoney.example.nz</p>
      <p class="contact__line">www.rimavalehoney.example.nz</p>
    </div>
    <div class="gold-band gold-band--bottom"></div>
  </section>

  <section class="card card--front" aria-label="Business card, brand side">
    <div class="gold-tab gold-tab--right"></div>
    <div class="brand">
      <span class="brand__dot"></span>
      <span class="brand__name">Rima Vale Honey</span>
    </div>
    <div class="gold-tab gold-tab--left"></div>
  </section>
</body>
</html>
```